Custom unique Stationary design for Logistics company

We need a custom, unique , elegant and luxurious full stationary design using our new logo, following these guidelines:
1- Business card: double sided, both sides uses the navy blue as the background main color (same as the code of the navy blue used in our logo).
2- envelope and folder: also use the same navy blue as the main background color.
3- book cover( notepad cover) : same thing with the navy blue
4- letterhead: feel free to use the combination of the colors in our logo.
5- rest of the items are up to your creativity

Target Market(s)

corporates and other businesses

Industry/Entity Type

Logistics and heavy machines contractors

Requirements
Must have
• Letterhead, business card, envelope, notepad cover, paper, file
Nice to have
• navy blue to be main background color for business card, envelope, notepad cover

```html
<!DOCTYPE html>
<html lang="en">
<head>
<meta charset="utf-8">
<title>Ridgeline Haulage Company – Business Card</title>
<link rel="stylesheet" href="https://fonts.googleapis.com/css2?family=Rubik:wght@400;500;600&display=swap">
<style>
  :root {
    --navy: #1b4f78;
    --orange: #e8612c;
    --white: #f4f5f6;
    --grey-text: #c9d3dc;
    --backdrop: #e4e4e4;
  }
  * { box-sizing: border-box; margin: 0; padding: 0; }
  html, body { width: 1200px; height: 885px; overflow: hidden; }
  body {
    background: var(--backdrop);
    font-family: "Rubik", Arial, sans-serif;
    position: relative;
  }
  .card {
    position: absolute;
    left: 290px;
    width: 620px;
    height: 354px;
    background: var(--navy);
    border-bottom: 3px solid var(--orange);
    border-radius: 2px;
    box-shadow: 0 14px 30px rgba(0,0,0,0.18);
    color: var(--white);
    overflow: hidden;
  }
  .card--front { top: 70px; }
  .card--back { top: 464px; }

  .brand {
    position: absolute;
    display: flex;
    align-items: center;
    gap: 12px;
    font-weight: 600;
    color: var(--white);
    white-space: nowrap;
  }
  .brand__dot {
    width: 16px; height: 16px;
    border-radius: 50%;
    background: var(--orange);
    flex: none;
  }
  .card--front .brand { right: 46px; top: 92px; font-size: 30px; letter-spacing: 0.5px; }
  .card--back .brand {
    left: 0; right: 0; top: 0; bottom: 0;
    justify-content: center;
    font-size: 46px; letter-spacing: 1px;
  }
  .card--back .brand__dot { width: 24px; height: 24px; }

  .divider {
    position: absolute;
    left: 266px; right: 40px; top: 196px;
    height: 1px;
    background: var(--white);
  }
  .person { position: absolute; left: 40px; top: 180px; white-space: nowrap; }
  .person__name {
    color: var(--orange);
    font-weight: 500;
    font-size: 22px;
    letter-spacing: 0.8px;
    text-transform: uppercase;
  }
  .person__title { font-weight: 500; font-size: 15px; margin-top: 2px; }

  .contacts { position: absolute; left: 40px; top: 250px; list-style: none; }
  .contacts li {
    display: flex; align-items: center; gap: 10px;
    font-size: 15px; line-height: 24px;
    white-space: nowrap;
  }
  .contacts svg { width: 16px; height: 16px; flex: none; }

  .address {
    position: absolute;
    right: 40px; top: 222px;
    text-align: right;
    font-style: normal;
    font-size: 15px;
    line-height: 22px;
    color: var(--grey-text);
    white-space: nowrap;
  }
</style>
</head>
<body>

  <section class="card card--front" aria-label="Business card, contact side">
    <div class="brand"><span class="brand__dot"></span>Ridgeline Haulage</div>

    <div class="divider"></div>

    <div class="person">
      <p class="person__name">Marcus Ellery</p>
      <p class="person__title">Managing Director</p>
    </div>

    <ul class="contacts">
      <li>
        <svg viewBox="0 0 16 16" aria-hidden="true"><path fill="#e8612c" d="M3.5 1.5l2.3 0.4 1 3-1.6 1.2a8 8 0 0 0 4.7 4.7l1.2-1.6 3 1 .4 2.3-2 1.5C6.8 13.5 2.5 9.2 2 3.5z"/></svg>
        555-018-2047
      </li>
      <li>
        <svg viewBox="0 0 16 16" aria-hidden="true"><rect x="1" y="3" width="14" height="10" fill="#e8612c"/><path d="M1.5 3.5L8 9l6.5-5.5" fill="none" stroke="#1b4f78" stroke-width="1.2"/></svg>
        hello@ridgelinehaul.com
      </li>
      <li>
        <svg viewBox="0 0 16 16" aria-hidden="true"><g fill="none" stroke="#e8612c" stroke-width="1.3"><circle cx="8" cy="8" r="6.5"/><ellipse cx="8" cy="8" rx="3" ry="6.5"/><path d="M1.5 8h13"/></g></svg>
        www.ridgelinehaul.com
      </li>
    </ul>

    <address class="address">
      Ridgeline Haulage Company<br>
      48 Foundry Lane, Suite 210<br>
      Millbrook, OH 45010
    </address>
  </section>

  <section class="card card--back" aria-label="Business card, brand side">
    <div class="brand"><span class="brand__dot"></span>Ridgeline Haulage</div>
  </section>

</body>
</html>
```